Fashion-Doll Website

I'm looking to create a new and better website for my growing fashion-doll brand, QUELLIE.

About me: I'm a Brooklyn-based artist, illustrator, and doll-maker and QUELLIE is the name of my doll. Quellie is a character doll (one girl) but she's not necessarily defined by any particular physical trait outside of the sculpt of the doll and her unique sense of style. For example, she could have pink hair and freckles or dark skin and green eyes, but she would still be "Quellie."

My partner and I created the current website ourselves using Adobe Muse. While it has served its purpose, we are not professional graphic or web designers, so I'm looking to graduate to a much more sophisticated and streamlined web design. I want the site to feel sweet and homespun but also hip and edgy. Because the site is so image heavy, I think black and white or black and off-white might be the best color palate, but I'm open to seeing other palates. Quellie's signature color is a muted lavender so maybe that could be integrated into the design. Here is the link:

www.QuellieDoll.example

I want the website to feel more like a shop and less like a gallery/info page. I'm now selling one-of-a-kind porcelain dolls, limited-edition resin dolls, face-plate necklaces, paper dolls, custom doll services, and printed Quellie throw pillows. I also need an interface that will allow me to create new categories, update inventory, and post new items easily.

I need to add new sections for press/articles, multiple image galleries (photography, products, illustrations, comics, and fan art), **collaboration projects, and several flash based doll "dress-up" games.

I would prefer a design that I can code/update myself using Adobe Muse. PSD files import into Muse, so I would prefer that you use them. I'm certainly not opposed to other designs, but I would prefer a design I can manage myself.

I'm including some photos and drawings of Quellie that express her look and vibe. I don't want to use these images in the web design necessarily (I think simple is best) but I thought they would be helpful in expressing the kind of girl she is and how I want the site to feel. I want to work with someone who has a clean, refined, yet whimsical aesthetic who can help me create a website that really expresses how special Quellie is.

Reason: I have had a family emergency come up and I can't devote time to this right now so I'm extending the deadline another 10 days.

Target Market(s)

young eccentrics, art collectors, fashion enthusiasts, and adult doll-collectors

Industry/Entity Type

Fashion

Requirements
Must have
• I need the following main categories: Info, Sales, Galleries, Press, and Dress-up. However, I don't necessarily want or expect the layout to be organized like the current website.

INFO:

*About Quellie (the character)

*Doll specifications: 27" porcelain doll, 22" porcelain doll, 22" resin doll, life-size doll (for window display)

*About the artist

SALES:

*Porcelain dolls

*Resin dolls

*Face-plate necklaces

*Pillows

*Custom doll/necklace info and inquiry form

GALLERIES:

*Photographs

*Collaboration projects

*Illustrations/Comics

*Fan Art/Contests

PRESS:

*An inventory of pdf's of articles about Quellie for users to download or view inside a reader online.

DRESS UP:

*Links to two interactive flash based dress-up games (interactive paper dolls)

Nice to have
• I hold online drawing and design contests from time to time so I would love to have a spot on the site reserved to host the rules and results of my contests.

Quellie has a large facebook and Instagram following so links to her social media would also be great.
instagram: @quelliedoll
facebook: fanpagehub.example/quelliedoll

Should not have
• I'm not looking to see anything too girly, too young, or too sexy.
Quellie is not Tessa, Marble Maiden, or Voxxi. She's a sophisticated young girl who is fresh, funky, and free-spirited.

```html
<!DOCTYPE html>
<html lang="en">
<head>
<meta charset="utf-8">
<title>Quellie Doll</title>
<link rel="stylesheet" href="https://fonts.googleapis.com/css2?family=Ubuntu:wght@300;400;500&family=Arimo:wght@400;500&display=swap">
<style>
  :root {
    --red: #d9231b;
    --red-dark: #b81a13;
    --ink: #333333;
    --text: #4a4a4a;
    --muted: #666666;
    --line: #d4d4d4;
    --hero-bg: #f5ebea;
    --footer-bg: #e7e8e9;
    --white: #ffffff;
  }
  html, body {
    margin: 0;
    width: 1200px;
    height: 1150px;
    overflow: hidden;
    background: var(--white);
    font-family: "Ubuntu", sans-serif;
    color: var(--ink);
  }
  .page { position: relative; width: 1200px; height: 1150px; }
  .abs { position: absolute; }

  .brand {
    left: 120px; top: 22px;
    font-family: "Ubuntu", sans-serif;
    font-weight: 300;
    font-size: 56px;
    letter-spacing: 4px;
    color: #222;
    margin: 0;
    line-height: 1;
  }
  .main-nav { top: 53px; left: 0; width: 1071px; }
  .main-nav a {
    position: absolute;
    font-family: "Arimo", sans-serif;
    font-weight: 500;
    font-size: 13px;
    color: #444;
    text-decoration: none;
    letter-spacing: 0.3px;
    white-space: nowrap;
  }

  .hero { left: 120px; top: 123px; width: 960px; height: 335px; background: var(--hero-bg); overflow: hidden; }
  .hero-title { position: absolute; left: 42px; top: 106px; margin: 0; font-size: 24px; font-weight: 400; color: var(--red); line-height: 1; }
  .hero-copy {
    position: absolute; left: 42px; top: 132px; width: 377px; margin: 0;
    font-size: 14px; line-height: 20px; text-transform: uppercase; text-align: justify;
    color: #555; letter-spacing: 0.2px;
  }
  .hero-dots { position: absolute; left: 41px; top: 258px; display: flex; gap: 5px; }
  .hero-dots span { width: 10px; height: 10px; border-radius: 50%; background: radial-gradient(circle at 40% 35%, #ddd, #888); }
  .hero-dots span.active { background: radial-gradient(circle at 40% 35%, #777, #222); }
  .hero-art {
    position: absolute; left: 430px; top: 0; width: 530px; height: 335px;
    background: linear-gradient(100deg, rgba(245,235,234,0) 0%, #8c7d8e 18%, #3f4f35 34%, #ece6e2 50%, #b73f3b 66%, #e9a09a 84%, rgba(245,235,234,0.6) 100%);
  }

  .welcome-title { left: 120px; top: 489px; margin: 0; font-size: 20px; font-weight: 500; color: var(--text); }
  .welcome-title em { font-style: normal; color: var(--red); }
  .welcome-art {
    left: 120px; top: 529px; width: 270px; height: 189px;
    background: linear-gradient(135deg, #cfc2e0 0%, #e9e4c4 35%, #c9c79a 55%, #eeeeee 80%, #e7c9d9 100%);
  }
  .welcome-copy { left: 404px; top: 527px; width: 366px; font-size: 13px; line-height: 18px; color: var(--ink); text-align: justify; }
  .welcome-copy p { margin: 0 0 18px; }

  .winner { left: 800px; top: 495px; width: 278px; height: 224px; border: 1px solid #dcdcdc; }
  .winner-title { margin: 0; position: absolute; left: 0; top: 13px; width: 100%; text-align: center; font-size: 15px; font-weight: 400; color: var(--red); }
  .winner-photo {
    position: absolute; left: 10px; top: 42px; width: 259px; height: 175px;
    background: linear-gradient(160deg, #8a7d6f 0%, #c6bfb3 45%, #efe9e6 70%, #b9aea3 100%);
  }
  .winner-ribbon { position: absolute; left: 10px; top: 165px; }
  .winner-ribbon span { position: absolute; left: 16px; top: 11px; font-size: 17px; color: var(--white); font-weight: 400; letter-spacing: 0.5px; }

  .rule { left: 120px; width: 960px; height: 1px; background: var(--line); }
  .contest-title { left: 120px; top: 776px; margin: 0; font-size: 15px; font-weight: 500; color: var(--text); }
  .btn {
    background: var(--red); color: var(--white); border: 1px solid var(--red-dark);
    border-radius: 2px; font-family: "Ubuntu", sans-serif; text-align: center;
    box-shadow: 0 1px 2px rgba(0,0,0,0.25);
  }
  .btn-submit { left: 928px; top: 770px; width: 148px; height: 30px; line-height: 30px; font-size: 12.5px; font-weight: 500; }

  .contest-tile { top: 832px; width: 220px; height: 140px; }
  .tile-1 { left: 120px; background: linear-gradient(135deg, #6f7a3a, #e9e4d6 50%, #2b2522); }
  .tile-2 { left: 366px; background: linear-gradient(135deg, #b6304a, #e8a0b0 45%, #202020); }
  .tile-3 { left: 612px; background: linear-gradient(135deg, #a7a98a, #4d4a4f 45%, #2c4d7a); }
  .tile-4 { left: 858px; background: linear-gradient(160deg, #6d9ad0, #d8d0c2 50%, #2a2220); }

  .newsletter { left: 120px; top: 998px; width: 958px; height: 74px; border: 1px solid #dcdcdc; }
  .newsletter h3 { position: absolute; left: 9px; top: 11px; margin: 0; font-size: 15px; font-weight: 400; color: #444; text-transform: uppercase; }
  .newsletter p { position: absolute; left: 10px; top: 29px; width: 270px; margin: 0; font-size: 12px; line-height: 18px; color: #333; }
  .field {
    position: absolute; top: 18px; width: 238px; height: 34px; border: 1px solid #d0d0d0;
    font-size: 12px; line-height: 34px; color: #666; padding-left: 5px; box-sizing: border-box;
  }
  .field-name { left: 303px; width: 240px; }
  .field-email { left: 557px; width: 240px; }
  .btn-signup { position: absolute; left: 822px; top: 18px; width: 108px; height: 34px; line-height: 34px; font-size: 16px; }

  .site-footer { left: 0; top: 1091px; width: 1200px; height: 59px; background: var(--footer-bg); border-top: 1px solid #cfd0d1; }
  .legal { position: absolute; left: 121px; top: 27px; font-family: "Arimo", sans-serif; font-size: 12px; color: #555; }
  .legal span { margin: 0 5px; }
  .social { position: absolute; top: 19px; left: 895px; display: flex; gap: 8px; }
  .social a { display: block; width: 24px; height: 24px; background: #8a8c8f; }
</style>
</head>
<body>
<div class="page">

  <header>
    <h1 class="brand abs">QUELLIE</h1>
    <nav class="main-nav abs">
      <a href="#" style="left:629px">HOME</a>
      <a href="#" style="left:702px">INFO</a>
      <a href="#" style="left:767px">SALES</a>
      <a href="#" style="left:839px">GALLERIES</a>
      <a href="#" style="left:939px">PRESS</a>
      <a href="#" style="left:1012px">DRESS UP</a>
    </nav>
  </header>

  <section class="hero abs">
    <h2 class="hero-title">QUELLIE IS A MODERN</h2>
    <p class="hero-copy">Take on the classic European fashion doll. Each element of Quellie is designed and handcrafted, from the heirloom-quality porcelain to the custom wigs and garments.</p>
    <div class="hero-dots"><span></span><span></span><span class="active"></span><span></span><span></span><span></span></div>
    <div class="hero-art" role="img" aria-label="Photograph of three Quellie dolls in lavender, platinum and red wigs wearing green, polka-dot and coral outfits"></div>
  </section>

  <h2 class="welcome-title abs">Welcome to <em>Quellie Doll !</em></h2>
  <div class="welcome-art abs" role="img" aria-label="Illustration of Quellie lounging on quilted cushions with a book and cats"></div>
  <div class="welcome-copy abs">
    <p>Quellie is a modern take on the classic European fashion doll. Each element of Quellie is designed and handcrafted, from the heirloom-quality porcelain to the custom wigs and garments. Her look embodies Brooklyn street-style, Manhattan sophistication, and the classic lines of yesterday. Quellie represents a new chapter in the venerable tradition of boutique doll-making.</p>
    <p>Quellie represents a new chapter in the venerable tradition of boutique doll-making.Quellie represents a new chapter in the venerable tradition of boutique doll-making.</p>
  </div>

  <aside class="winner abs">
    <h3 class="winner-title">WINNER OF THE MONTH</h3>
    <div class="winner-photo" role="img" aria-label="Photograph of the winning doll in a white blouse and floral skirt on outdoor steps"></div>
    <div class="winner-ribbon">
      <svg width="110" height="40" viewBox="0 0 110 40" aria-hidden="true">
        <polygon points="0,0 96,0 110,40 0,40" fill="#d9231b"/>
        <polygon points="96,0 104,0 110,40" fill="#b81a13"/>
      </svg>
      <span>WINNER</span>
    </div>
  </aside>

  <div class="rule abs" style="top:760px"></div>
  <h2 class="contest-title abs">Drawing/ Design Contests</h2>
  <a class="btn btn-submit abs">SUBMIT YOUR DESIGNS</a>
  <div class="rule abs" style="top:812px"></div>

  <div class="contest-tile tile-1 abs" role="img" aria-label="Photograph of a doll with platinum curls and a black bow"></div>
  <div class="contest-tile tile-2 abs" role="img" aria-label="Photograph of a doll with a pink bob in black lace"></div>
  <div class="contest-tile tile-3 abs" role="img" aria-label="Photograph of a dark-haired doll with a blue ruffled collar outdoors"></div>
  <div class="contest-tile tile-4 abs" role="img" aria-label="Photograph of a doll in a black dress with red roses in front of a building"></div>

  <section class="newsletter abs">
    <h3>Newsletter Sign Up</h3>
    <p>Quellie is a modern take on the classic European fashion doll.</p>
    <div class="field field-name">Enter your name</div>
    <div class="field field-email">Enter your E-mail</div>
    <a class="btn btn-signup">SIGN UP</a>
  </section>

  <footer class="site-footer abs">
    <div class="legal">© 2013 Quellie Doll<span>|</span>Privacy Notice<span>|</span>Conditions of Use</div>
    <div class="social">
      <a href="#" aria-label="Social link 1"></a>
      <a href="#" aria-label="Social link 2"></a>
      <a href="#" aria-label="Social link 3"></a>
      <a href="#" aria-label="Social link 4"></a>
      <a href="#" aria-label="Social link 5"></a>
      <a href="#" aria-label="News feed"></a>
    </div>
  </footer>

</div>
</body>
</html>
```